R7M Horizon Business Card Design

We need a business card created for our New Business "R7M Horizon"<br/><br/>The business card design is up to you however the following information must be on the business card:<br/><br/>Front of the business card -<br/>Email :darrenp@r7mhorizon.nz<br/>Mobile: +64 (0) 22 4870 619<br/>Website: www.r7mhorizon.nz<br/>Card Owner Name: Darren Paltrow<br/>Company Title: Business Development Manager<br/>Slogan: "The BEST of both worlds". <br/>Logo On the front attached to the design brief<br/><br/>On the back: <br/>Space on the back for 4 more versions of the logo across the bottom of the card indicating different subsidiary brands - R7M Coffee, R7M Arts, R7M ?? (The card will be used for all of these brands - We Will add the extra subsidiary logos to the design once the design is finished (We are a graphics design team). <br/><br/>Other than that we want a premium feeling logo that remains universally usable depending on the business entity that we are using the card for. The use of bright bold colours would be great but we still want the card to feel premium.
Target Market(s)
Gift Design and Manufacturing Companies
Contact Information for Business Card
Front of the business card -
Email :darrenp@r7mhorizon.nz
Mobile: +64 (0) 22 4870 619
Website: www.r7mhorizon.nz
Card Owner Name: Darren Paltrow
Company Title: Business Development Manager
Slogan: "The BEST of both worlds".
Logo On the front attached to the design brief

```html
<!DOCTYPE html>
<html lang="en">
<head>
<meta charset="utf-8">
<title>R7M Horizon – Business Card</title>
<link rel="stylesheet" href="https://fonts.googleapis.com/css2?family=Montserrat:ital,wght@1,800&family=Open+Sans:wght@400;600;700&display=swap">
<style>
  :root {
    --brand-blue: #3343a6;
    --card-white: #ffffff;
    --ink: #2a2a2a;
    --rule: #7d86c9;
    --stage: #2b2b2d;
  }
  * { box-sizing: border-box; margin: 0; padding: 0; }
  html, body {
    width: 1200px; height: 900px; overflow: hidden;
    background: var(--stage);
    font-family: "Open Sans", Arial, sans-serif;
  }
  .card {
    position: absolute; left: 300px; width: 600px; height: 343px;
    border-radius: 26px; overflow: hidden;
  }

  /* Back of card */
  .card-back { top: 88px; background: var(--brand-blue); color: var(--card-white); }
  .card-back .brand-name {
    position: absolute; left: 0; right: 0; top: 122px;
    text-align: center; font-size: 44px;
  }
  .card-back .slogan {
    position: absolute; left: 0; right: 0; bottom: 44px;
    text-align: center; font-size: 15px; letter-spacing: .3px;
  }
  .slogan .arrow { font-size: 10px; margin: 0 6px; vertical-align: 1px; }
  .slogan strong { font-weight: 700; }

  .brand-name {
    font-family: "Open Sans", Arial, sans-serif; font-weight: 700;
    letter-spacing: 1px; line-height: 1; white-space: nowrap;
  }

  /* Front of card */
  .card-front { top: 475px; background: var(--card-white); color: var(--ink); }
  .accent-bar { position: absolute; left: 0; top: 120px; width: 14px; height: 40px; background: var(--brand-blue); }
  .owner { position: absolute; left: 32px; top: 112px; }
  .owner-name {
    font-family: "Montserrat", Arial, sans-serif; font-style: italic; font-weight: 800;
    font-size: 27px; color: var(--brand-blue); letter-spacing: 1px; line-height: 1.05;
    text-transform: uppercase;
  }
  .owner-title { font-size: 14px; color: var(--ink); margin-top: 2px; }
  .divider { position: absolute; left: 32px; right: 30px; top: 172px; height: 1px; background: var(--rule); }

  .contact { position: absolute; right: 30px; top: 26px; list-style: none; text-align: right; font-size: 14px; line-height: 21px; }
  .contact li { display: flex; justify-content: flex-end; align-items: center; gap: 7px; }
  .contact svg { width: 12px; height: 12px; fill: none; stroke: var(--brand-blue); stroke-width: 1.6; }

  .card-front .brand-name {
    position: absolute; left: 44px; bottom: 48px;
    font-size: 40px; color: var(--brand-blue);
  }

  .slogan-tab {
    position: absolute; right: 0; top: 196px; height: 38px; width: 240px;
    background: var(--brand-blue); color: var(--card-white);
    border-radius: 19px 0 0 19px; display: flex; align-items: center;
    padding-left: 20px; font-size: 14px;
  }
  .slogan-tab strong { font-weight: 700; margin: 0 4px; }
</style>
</head>
<body>

<section class="card card-back" aria-label="Card back">
  <p class="brand-name">R7M Horizon</p>
  <p class="slogan"><span class="arrow">◀</span>The <strong>BEST</strong> of both worlds<span class="arrow">▶</span></p>
</section>

<section class="card card-front" aria-label="Card front">
  <ul class="contact">
    <li>+64 (0) 22 4870 619
      <svg viewBox="0 0 12 12"><path d="M3 1.5 L4.6 3.8 L3.6 5 Q4.8 7.3 7 8.4 L8.2 7.4 L10.5 9 L9.4 10.6 Q4.5 10 1.4 2.6 Z"/></svg></li>
    <li>darrenp@r7mhorizon.nz
      <svg viewBox="0 0 12 12"><rect x="1" y="2.5" width="10" height="7" rx="1"/><path d="M1.3 3 L6 6.6 L10.7 3"/></svg></li>
    <li>www.r7mhorizon.nz
      <svg viewBox="0 0 12 12"><circle cx="6" cy="6" r="4.8"/><ellipse cx="6" cy="6" rx="2" ry="4.8"/><path d="M1.2 6 H10.8"/></svg></li>
  </ul>

  <span class="accent-bar"></span>
  <div class="owner">
    <h1 class="owner-name">Darren Paltrow</h1>
    <p class="owner-title">Business Development Manager</p>
  </div>
  <span class="divider"></span>

  <p class="slogan-tab">The<strong>BEST</strong>of both worlds</p>

  <p class="brand-name">R7M Horizon</p>
</section>

</body>
</html>
```